TALMORK

The business want a professional looking business card. We have a scetch we will add but want the extra upgrade, and would like more suggestions for variations of our business cards.

```html
<!DOCTYPE html>
<html lang="en">
<head>
<meta charset="utf-8">
<title>TALMORK Business Card</title>
<link rel="stylesheet" href="https://fonts.googleapis.com/css2?family=Montserrat:wght@400;700&family=Playfair+Display:wght@500;700&display=swap">
<style>
  :root {
    --stage: #1b1b1b;
    --card-light: #f4f4f4;
    --card-dark: #1c1c1c;
    --bronze: #76501d;
    --gold: #c8a04b;
    --ink: #1e1e1e;
    --watermark: #e6e6e6;
  }
  * { margin: 0; padding: 0; box-sizing: border-box; }
  html, body {
    width: 1200px;
    height: 1059px;
    overflow: hidden;
    background: var(--stage);
  }
  .canvas {
    position: relative;
    width: 1200px;
    height: 1059px;
  }
  .card {
    position: absolute;
    width: 690px;
    height: 392px;
    border-radius: 18px;
    overflow: hidden;
  }
  .card-front { left: 256px; top: 89px; background: var(--card-light); }
  .card-back { left: 255px; top: 547px; background: var(--card-dark); }

  .front-watermark {
    position: absolute;
    left: 352px;
    top: 0;
    width: 338px;
    height: 392px;
    background: radial-gradient(circle at 55% 50%, var(--watermark) 0%, rgba(230,230,230,0.4) 45%, rgba(244,244,244,0) 72%);
  }

  .brand-block {
    position: absolute;
    left: 37px;
    top: 50px;
    text-align: center;
    color: var(--bronze);
    font-family: "Playfair Display", serif;
  }
  .brand-name {
    font-size: 50px;
    font-weight: 500;
    letter-spacing: 0.16em;
    line-height: 1;
    margin-right: -0.16em;
  }
  .brand-since {
    margin-top: 12px;
    font-size: 14px;
    font-weight: 700;
    letter-spacing: 0.42em;
    margin-right: -0.42em;
  }

  .accent-bar {
    position: absolute;
    left: 0;
    top: 174px;
    width: 21px;
    height: 42px;
    background: var(--bronze);
  }
  .person {
    position: absolute;
    left: 38px;
    top: 167px;
    font-family: "Montserrat", sans-serif;
  }
  .person-name {
    font-size: 24px;
    font-weight: 700;
    color: var(--bronze);
    line-height: 1.2;
  }
  .person-role {
    font-size: 18px;
    color: var(--ink);
    line-height: 1.2;
  }

  .contact-list {
    position: absolute;
    left: 37px;
    top: 252px;
    list-style: none;
    font-family: "Montserrat", sans-serif;
    font-size: 19.5px;
    color: var(--ink);
  }
  .contact-item {
    display: flex;
    align-items: center;
    height: 36px;
  }
  .contact-icon {
    width: 15px;
    height: 15px;
    margin-right: 10px;
    fill: var(--bronze);
  }

  .back-pattern {
    position: absolute;
    inset: 0;
    background: linear-gradient(100deg, #121212 0%, #1a1a1a 40%, #3a3a3a 75%, #5a5a5a 100%);
  }
  .back-logo {
    position: absolute;
    left: 466px;
    top: 170px;
    width: 160px;
    text-align: center;
    font-family: "Playfair Display", serif;
    color: var(--gold);
  }
  .back-mark {
    width: 44px;
    height: 44px;
    margin: 0 auto 22px;
    border-radius: 50%;
    background: var(--gold);
  }
  .back-name {
    font-size: 27px;
    font-weight: 500;
    letter-spacing: 0.14em;
    margin-right: -0.14em;
    line-height: 1;
  }
  .back-since {
    margin-top: 6px;
    font-size: 7.5px;
    font-weight: 700;
    letter-spacing: 0.4em;
    margin-right: -0.4em;
  }
</style>
</head>
<body>
<main class="canvas">

  <section class="card card-front">
    <div class="front-watermark" role="img" aria-label="Faint oversized decorative motif"></div>

    <div class="brand-block">
      <div class="brand-name">TALMORK</div>
      <div class="brand-since">SINCE 2026</div>
    </div>

    <div class="accent-bar"></div>
    <div class="person">
      <div class="person-name">Anders Holm Vikestad</div>
      <div class="person-role">CEO &amp; Founder</div>
    </div>

    <ul class="contact-list">
      <li class="contact-item">
        <svg class="contact-icon" viewBox="0 0 24 24" aria-hidden="true"><path d="M6.6 10.8a15.1 15.1 0 0 0 6.6 6.6l2.2-2.2a1 1 0 0 1 1-.25 11.4 11.4 0 0 0 3.6.57 1 1 0 0 1 1 1V20a1 1 0 0 1-1 1A17 17 0 0 1 3 4a1 1 0 0 1 1-1h3.5a1 1 0 0 1 1 1c0 1.25.2 2.45.57 3.57a1 1 0 0 1-.25 1z"/></svg>
        <span>004795550142</span>
      </li>
      <li class="contact-item">
        <svg class="contact-icon" viewBox="0 0 24 24" aria-hidden="true"><path d="M2 9l10-6 10 6v11H2z M4 10.2V18h16v-7.8l-8 5z"/></svg>
        <span>talmork.llc@mailbox.com</span>
      </li>
      <li class="contact-item">
        <svg class="contact-icon" viewBox="0 0 24 24" aria-hidden="true"><circle cx="12" cy="12" r="10"/></svg>
        <span>www.talmork.llc</span>
      </li>
    </ul>
  </section>

  <section class="card card-back">
    <div class="back-pattern" role="img" aria-label="Repeating tone-on-tone ornamental pattern fading from black to grey"></div>
    <div class="back-logo">
      <div class="back-mark"></div>
      <div class="back-name">TALMORK</div>
      <div class="back-since">SINCE 2026</div>
    </div>
  </section>

</main>
</body>
</html>
```